Orvane Mechanical - Letterhead

We are a plumbing and hvac company based in Calgary. This letterhead will be on our quotes, invoices, preventative maintenance proposals etc.

```html
<!DOCTYPE html>
<html lang="en">
<head>
<meta charset="UTF-8">
<title>Orvane Mechanical – Letterhead</title>
<link rel="stylesheet" href="https://fonts.googleapis.com/css2?family=Nunito+Sans:wght@400;800&display=swap">
<style>
  :root {
    --backdrop: #d6d6d6;
    --paper: #ffffff;
    --brand-orange: #ef6236;
    --brand-blue: #3a78bd;
    --watermark: #fce8e1;
  }
  * { margin: 0; padding: 0; box-sizing: border-box; }
  html, body {
    width: 1200px;
    height: 1200px;
    overflow: hidden;
    background: var(--backdrop);
    font-family: "Nunito Sans", sans-serif;
  }
  .letterhead {
    position: absolute;
    left: 300px;
    top: 176px;
    width: 600px;
    height: 848px;
    background: var(--paper);
  }
  .band {
    position: absolute;
    left: 154px;
    width: 291px;
  }
  .band-top { top: 0; }
  .band-bottom { bottom: 0; }
  .band .stripe-orange { height: 31px; background: var(--brand-orange); }
  .band .stripe-blue { height: 6px; background: var(--brand-blue); }

  .brand {
    position: absolute;
    left: 160px;
    top: 56px;
    width: 130px;
    display: flex;
    flex-direction: column;
    align-items: center;
  }
  .brand-dot {
    width: 24px;
    height: 24px;
    border-radius: 50%;
    background: var(--brand-orange);
    margin-bottom: 8px;
  }
  .brand-name {
    font-weight: 800;
    font-size: 13px;
    line-height: 1.15;
    text-align: center;
    text-transform: uppercase;
    letter-spacing: 0.5px;
    color: var(--brand-blue);
  }
  .divider {
    position: absolute;
    left: 298px;
    top: 76px;
    width: 1px;
    height: 58px;
    background: var(--brand-orange);
  }
  .contact {
    position: absolute;
    left: 310px;
    top: 84px;
    list-style: none;
    font-size: 8.5px;
    line-height: 11px;
    color: var(--brand-blue);
  }
  .watermark {
    position: absolute;
    left: 95px;
    top: 219px;
    width: 410px;
    height: 410px;
    border-radius: 50%;
    background: var(--watermark);
  }
</style>
</head>
<body>
  <main class="letterhead">
    <div class="band band-top">
      <div class="stripe-orange"></div>
      <div class="stripe-blue"></div>
    </div>

    <header>
      <div class="brand">
        <span class="brand-dot"></span>
        <span class="brand-name">Orvane<br>Mechanical Inc</span>
      </div>
      <div class="divider"></div>
      <ul class="contact">
        <li>Company address, 0000</li>
        <li>000 000 000</li>
        <li>contact@orvanemechanical.com</li>
        <li>www.orvanemechanical.com</li>
      </ul>
    </header>

    <div class="watermark" role="img" aria-label="Faint brand watermark"></div>

    <div class="band band-bottom">
      <div class="stripe-blue"></div>
      <div class="stripe-orange"></div>
    </div>
  </main>
</body>
</html>
```